Künstlerisches CD-Cover für Album
Zielgruppe
Ich bin ein Künstler im musikalischen Bereich. Meine Musikrichtung ist kombiniert aus den Bereichen des Rapps und dem Gesang. Mein Stil ist eher Gefühlvoll. Passend dazu suche ich ein echt künstleriches CD-Cover für mein Album >>> Spur im Nebel <<< .
Aufgabenstellung
Ich lege besonderen Wert auf echt kreative und künstlerische Fähigkeiten bei der Umsetzug des CD-Covers. Dieses Cover sollte ein echter Blickfang werden und zu meinem Album Namens >>>Spur im Nebel<<< passen.
Dabei ist folgendes Besonders zu Beachten:
(Albumtitel und mein Künstlername sollte auf die Frontansicht)
Spur im Nebel
Jonas Brehm
(Auf die Rückseite des Album-Covers sollten die Songtitel, Songlänge, Gesamtlänge sowie die weiteren Infos stehen)
1. Auftakt (Tobi) 1:06
2. Spur im Nebel 3:36
3. Nachtlicht (feat. Sven) 3:52
4. Ohne dich 3:22
5. Kopf hoch 3:09
6. Zuhause 2:44
7. Für Papa 3:48
8. Letzter Zug 3:45
9. Herz verloren (feat. Sven) 3:15
10. Gute Tage 3:18
11. Bleib hier 3:21
12. Schicksal 2:47
13. Mein eigener Weg 3:13
14. Kein Plan 3:00
15. Winter 2:51
16. Lass los 3:58
17. Blick nach vorn 3:25
18. Spur im Nebel 3:36
58Min. 0Sek.
Texte & Songwriting by Jonas Brehm I Produziert im Nachtfalke Studio by Sven Ulrich Grabinski I Foto by Helmut K. Fotografie
(weitere Informationen)
>>> Das CD-Cover ist bestimmt für ein vierseitigen Druck und der CD (Voderseite, Rückseite, Innenseite Links, Innenseite Rechts und CD)
Das hochgeladene Fotomaterial sollte im Design mit eingebunden werden. Am besten wäre das Foto mit meiner Wenigkeit auf der Innenseite Links und das andere vorhandene Foto auf der CD selber zu intigrieren. Natürlich bin ich aber auch Offen für Alles und vertraue auf eure künstlerischen Fähigkeiten.
Viel Spaß :)

```html
<!DOCTYPE html>
<html lang="de">
<head>
<meta charset="utf-8">
<title>Spur im Nebel – CD-Gestaltung</title>
<link rel="stylesheet" href="https://fonts.googleapis.com/css2?family=Bitter:wght@700&family=Leckerli+One&display=swap">
<style>
  :root {
    --magenta: #a5195c;
    --pink: #e2097e;
    --white: #ffffff;
    --paper: #ffffff;
    --mist-top: #8c9bb0;
    --mist-mid: #5e6a7c;
    --rock: #3a2f26;
    --heart-red: #d8302f;
    --dot-pink: #e9b9d2;
    --ink-line: #222222;
  }
  html, body {
    margin: 0;
    padding: 0;
    width: 1200px;
    height: 852px;
    overflow: hidden;
    background: var(--paper);
  }
  .sheet { display: block; width: 1200px; height: 852px; }
  .panel-bg { fill: var(--magenta); }
  .panel-frame { filter: drop-shadow(0 3px 3px rgba(0,0,0,0.35)); }
  .disc-white { fill: var(--white); }
  .ring-white { fill: none; stroke: var(--white); stroke-width: 1.2; }
  .ring-pink { fill: none; stroke: var(--pink); stroke-width: 1; }
  .fill-pink { fill: var(--pink); }
  .heart-edge { fill: none; stroke: var(--white); stroke-width: 2; }
  .tracklist {
    font-family: "Bitter", Georgia, serif;
    font-weight: 700;
    font-size: 9.6px;
    fill: var(--white);
  }
  .script-title, .script-artist {
    font-family: "Leckerli One", cursive;
    fill: var(--white);
  }
  .script-title { font-size: 20px; }
  .script-artist { font-size: 18px; }
  .disc-title { font-size: 23px; }
  .disc-artist { font-size: 14px; }
  .disc-outline { fill: none; stroke: var(--ink-line); stroke-width: 1; }
  .crop-mark { fill: none; stroke: var(--ink-line); stroke-width: 0.8; }
  .cut-guide { fill: none; stroke: #555; stroke-width: 0.8; stroke-dasharray: 10 8; }
</style>
</head>
<body>
<svg class="sheet" viewBox="0 0 1200 852" xmlns="http://www.w3.org/2000/svg">
  <defs>
    <linearGradient id="mist-photo" x1="0" y1="0" x2="0" y2="1">
      <stop offset="0" stop-color="var(--mist-top)"/>
      <stop offset="0.55" stop-color="var(--mist-mid)"/>
      <stop offset="0.7" stop-color="var(--heart-red)"/>
      <stop offset="1" stop-color="var(--rock)"/>
    </linearGradient>
    <linearGradient id="portrait-photo" x1="0" y1="0" x2="0" y2="1">
      <stop offset="0" stop-color="#2b2b30"/>
      <stop offset="0.6" stop-color="#8a8a90"/>
      <stop offset="1" stop-color="#b9b6b4"/>
    </linearGradient>
    <linearGradient id="halftone-fade-x" x1="0" y1="0" x2="1" y2="0">
      <stop offset="0" stop-color="var(--dot-pink)" stop-opacity="0.75"/>
      <stop offset="1" stop-color="var(--dot-pink)" stop-opacity="0"/>
    </linearGradient>
    <linearGradient id="halftone-fade-y" x1="0" y1="0" x2="0" y2="1">
      <stop offset="0" stop-color="var(--dot-pink)" stop-opacity="0.7"/>
      <stop offset="1" stop-color="var(--dot-pink)" stop-opacity="0"/>
    </linearGradient>
    <linearGradient id="halftone-disc" x1="0" y1="0" x2="0" y2="1">
      <stop offset="0" stop-color="var(--pink)" stop-opacity="0"/>
      <stop offset="1" stop-color="var(--pink)" stop-opacity="0.75"/>
    </linearGradient>
    <clipPath id="clip-inside-left"><rect x="105" y="68" width="309" height="308"/></clipPath>
    <clipPath id="clip-inside-right"><rect x="434" y="68" width="310" height="308"/></clipPath>
    <clipPath id="clip-back"><rect x="105" y="431" width="310" height="310"/></clipPath>
    <clipPath id="clip-front"><rect x="434" y="431" width="310" height="310"/></clipPath>
    <clipPath id="clip-disc"><circle cx="977" cy="406" r="178"/></clipPath>
    <path id="heart-window" d="M424,130 C400,80 340,60 300,78 C255,98 235,150 242,200 C252,270 330,320 424,378 C518,320 596,270 606,200 C613,150 593,98 548,78 C508,60 448,80 424,130 Z"/>
  </defs>

  <!-- Inside left -->
  <g class="panel inside-left">
    <rect class="panel-bg panel-frame" x="105" y="68" width="309" height="308"/>
    <g clip-path="url(#clip-inside-left)">
      <rect x="105" y="68" width="110" height="308" fill="url(#halftone-fade-x)" role="img" aria-label="Rasterpunkt-Muster"/>
      <circle class="disc-white" cx="158" cy="93" r="38"/>
      <circle class="disc-white" cx="175" cy="378" r="65"/>
      <circle class="ring-pink" cx="203" cy="308" r="41"/>
      <circle class="ring-white" cx="249" cy="334" r="20"/>
      <use href="#heart-window" fill="url(#mist-photo)" role="img" aria-label="Foto: rotes Herz aus Stein auf einem Felsen vor einem Wasserfall"/>
      <use href="#heart-window" class="heart-edge"/>
      <circle class="ring-white" cx="385" cy="98" r="20"/>
    </g>
  </g>

  <!-- Inside right -->
  <g class="panel inside-right">
    <rect class="panel-bg panel-frame" x="434" y="68" width="310" height="308"/>
    <g clip-path="url(#clip-inside-right)">
      <rect x="614" y="68" width="130" height="120" fill="url(#halftone-fade-y)" role="img" aria-label="Rasterpunkt-Muster"/>
      <use href="#heart-window" fill="url(#mist-photo)" role="img" aria-label="Foto: rotes Herz aus Stein auf einem Felsen vor einem Wasserfall"/>
      <use href="#heart-window" class="heart-edge"/>
      <circle class="disc-white" cx="713" cy="368" r="45"/>
      <circle class="ring-pink" cx="684" cy="314" r="58"/>
    </g>
  </g>

  <!-- Back cover -->
  <g class="panel back-cover">
    <rect class="panel-bg panel-frame" x="105" y="431" width="310" height="310"/>
    <g clip-path="url(#clip-back)">
      <circle class="disc-white" cx="150" cy="504" r="82"/>
      <rect x="105" y="431" width="85" height="155" fill="url(#halftone-fade-x)" role="img" aria-label="Rasterpunkt-Muster"/>
      <circle class="fill-pink" cx="221" cy="492" r="60"/>
      <circle class="disc-white" cx="365" cy="735" r="80"/>
      <circle class="fill-pink" cx="340" cy="696" r="57"/>
    </g>
    <text class="tracklist" text-anchor="middle">
      <tspan x="259" y="449">1. Auftakt (Tobi) 1:12</tspan>
      <tspan x="259" dy="10.95">2. Spur im Nebel 3:41</tspan>
      <tspan x="259" dy="10.95">3. Nachtlicht (feat. Sven) 3:47</tspan>
      <tspan x="259" dy="10.95">4. Ohne dich 3:19</tspan>
      <tspan x="259" dy="10.95">5. Kopf hoch 3:05</tspan>
      <tspan x="259" dy="10.95">6. Zuhause 2:58</tspan>
      <tspan x="259" dy="10.95">7. Für Papa 3:44</tspan>
      <tspan x="259" dy="10.95">8. Letzter Zug 3:39</tspan>
      <tspan x="259" dy="10.95">9. Herz verloren (feat. Sven) 3:11</tspan>
      <tspan x="259" dy="10.95">10. Gute Tage 3:24</tspan>
      <tspan x="259" dy="10.95">11. Bleib hier 3:16</tspan>
      <tspan x="259" dy="10.95">12. Schicksal 2:53</tspan>
      <tspan x="259" dy="10.95">13. Mein eigener Weg 3:08</tspan>
      <tspan x="259" dy="10.95">14. Kein Plan 3:02</tspan>
      <tspan x="259" dy="10.95">15. Winter 2:49</tspan>
      <tspan x="259" dy="10.95">16. Lass los 3:55</tspan>
      <tspan x="259" dy="10.95">17. Blick nach vorn 3:27</tspan>
      <tspan x="259" dy="10.95">18. Spur im Nebel (Akustik) 3:30</tspan>
      <tspan x="259" dy="21.9">58Min. 0Sek.</tspan>
      <tspan x="259" dy="21.9">Texte &amp; Songwriting by Jonas Brehm</tspan>
      <tspan x="259" dy="10.95">Produziert im Nachtfalke Studio by Sven Ulrich Grabinski</tspan>
      <tspan x="259" dy="10.95">Foto by Helmut K. Fotografie</tspan>
    </text>
  </g>

  <!-- Front cover -->
  <g class="panel front-cover">
    <rect class="panel-bg panel-frame" x="434" y="431" width="310" height="310"/>
    <g clip-path="url(#clip-front)">
      <circle class="disc-white" cx="640" cy="480" r="62"/>
      <circle class="disc-white" cx="472" cy="590" r="100"/>
      <rect x="434" y="515" width="50" height="150" fill="url(#halftone-fade-x)" role="img" aria-label="Rasterpunkt-Muster"/>
      <path class="panel-bg" d="M434,431 L596,431 C594,470 580,490 545,494 C510,497 470,490 434,500 Z"/>
      <circle class="disc-white" cx="741" cy="507" r="26"/>
      <circle fill="url(#portrait-photo)" cx="589" cy="589" r="122" role="img" aria-label="Porträtfoto des Künstlers, sitzend vor Felsen, mit rotem Herz in den Händen"/>
      <circle class="ring-white" cx="589" cy="589" r="113"/>
      <circle class="ring-white" cx="700" cy="479" r="8"/>
      <circle class="fill-pink" cx="707" cy="674" r="19"/>
      <circle class="ring-white" cx="484" cy="484" r="17"/>
      <circle class="ring-white" cx="507" cy="707" r="17"/>
      <circle class="disc-white" cx="555" cy="741" r="27"/>
    </g>
    <text class="script-title" x="439" y="454">Spur im Nebel</text>
    <text class="script-artist" x="725" y="725" text-anchor="end">Jonas Brehm</text>
  </g>

  <!-- Disc label -->
  <g class="disc-label">
    <g clip-path="url(#clip-disc)">
      <rect x="799" y="228" width="356" height="356" fill="url(#mist-photo)" role="img" aria-label="Foto: rotes Herz aus Stein auf einem Felsen vor einem Wasserfall"/>
      <rect x="860" y="510" width="240" height="80" fill="url(#halftone-disc)" role="img" aria-label="Rasterpunkt-Muster"/>
      <path class="fill-pink" d="M790,340 C840,326 900,345 960,338 C1010,332 1030,300 1038,230 L1038,200 L790,200 Z"/>
      <circle class="ring-white" cx="840" cy="333" r="14"/>
      <circle class="ring-pink" cx="1039" cy="277" r="23"/>
    </g>
    <circle class="disc-outline" cx="977" cy="406" r="178"/>
    <circle class="disc-white" cx="977" cy="406" r="25" stroke="var(--ink-line)" stroke-width="0.8"/>
    <text class="script-artist disc-artist" x="955" y="275" text-anchor="middle">Jonas Brehm</text>
    <text class="script-title disc-title" x="925" y="311" text-anchor="middle">Spur im Nebel</text>
  </g>

  <!-- Print marks -->
  <g class="print-marks">
    <g class="crop-mark">
      <circle cx="977" cy="207" r="5"/><path d="M969,207 H985 M977,199 V215"/>
      <circle cx="779" cy="405" r="5"/><path d="M771,405 H787 M779,397 V413"/>
      <circle cx="1175" cy="405" r="5"/><path d="M1167,405 H1183 M1175,397 V413"/>
      <circle cx="977" cy="603" r="5"/><path d="M969,603 H985 M977,595 V611"/>
    </g>
    <path class="cut-guide" d="M773,603 H1173 V190"/>
  </g>
</svg>
</body>
</html>
```